BildeVOLD buisnesscard

Hey :) I need a modern buisnesscard for my company BildeVOLD
It most have:
Dagligleder og Fotograf: Henrik Audun Strandvik

Mob: +4791264085
Epost: post@bildevold.example
Adresse: Kvernbakken9, 6040 Langevåg

Facbook and instagram logo with text BildeVOLD

BildeVOLD logo

It Company

```html
<!DOCTYPE html>
<html lang="no">
<head>
<meta charset="utf-8">
<title>BildeVOLD – visittkort</title>
<link rel="stylesheet" href="https://fonts.googleapis.com/css2?family=Open+Sans:wght@400;600;700&display=swap">
<style>
  :root {
    --backdrop: #3b3b3b;
    --card: #ffffff;
    --brand-blue: #2580b3;
    --brand-pink: #cc4a8c;
    --text-light: #ffffff;
  }
  * { box-sizing: border-box; margin: 0; padding: 0; }
  html, body {
    width: 1105px; height: 1200px; overflow: hidden;
    background: var(--backdrop);
    font-family: "Open Sans", sans-serif;
  }
  .canvas { position: relative; width: 1105px; height: 1200px; }
  .card {
    position: absolute; left: 193px; width: 720px; height: 410px;
    background: var(--card); overflow: hidden;
  }
  .card--front { top: 167px; }
  .card--back { top: 623px; }
  .card__shapes { position: absolute; inset: 0; width: 100%; height: 100%; }

  .wordmark {
    position: absolute; color: var(--brand-blue);
    font-weight: 700; line-height: 1; white-space: nowrap;
  }
  .wordmark--front { left: 386px; top: 140px; font-size: 54px; }

  .contact { position: absolute; left: 30px; top: 200px; color: var(--text-light); }
  .contact__name { font-size: 24px; font-weight: 600; line-height: 1.2; }
  .contact__role { font-size: 17px; line-height: 1.3; margin-bottom: 14px; }
  .contact__list { list-style: none; }
  .contact__item {
    display: flex; align-items: center; gap: 10px;
    font-size: 17px; line-height: 27.5px;
  }
  .contact__icon { width: 16px; height: 16px; flex: none; }
  .contact__address { font-size: 17px; margin-top: 8px; padding-left: 6px; }

  .back-mark {
    position: absolute; left: 0; right: 0; top: 165px;
    display: flex; justify-content: center; align-items: center; gap: 16px;
  }
  .back-mark__square { width: 46px; height: 46px; background: var(--brand-pink); }
  .back-mark__name { color: var(--brand-blue); font-size: 62px; font-weight: 700; line-height: 1; }

  .social {
    position: absolute; left: 0; right: 0; top: 337px;
    display: flex; justify-content: center; align-items: center; gap: 6px;
  }
  .social__rule { width: 125px; height: 2px; }
  .social__rule--left { background: linear-gradient(to right, rgba(37,128,179,0), var(--brand-blue)); margin-right: 6px; }
  .social__rule--right { background: linear-gradient(to left, rgba(37,128,179,0), var(--brand-blue)); margin-left: 6px; }
  .social__badge {
    width: 36px; height: 36px; border-radius: 50%;
    border: 2px solid var(--brand-blue);
  }
</style>
</head>
<body>
<main class="canvas">

  <section class="card card--front" aria-label="Forside">
    <svg class="card__shapes" viewBox="0 0 720 410" preserveAspectRatio="none" aria-hidden="true">
      <rect width="720" height="410" fill="var(--brand-blue)"/>
      <polygon points="82,0 720,0 720,218 543,384" fill="var(--card)"/>
      <line x1="732" y1="198" x2="539" y2="376" stroke="var(--brand-blue)" stroke-width="10"/>
      <line x1="76" y1="-4" x2="545" y2="386" stroke="var(--brand-pink)" stroke-width="10"/>
    </svg>

    <div class="wordmark wordmark--front">BildeVOLD</div>

    <div class="contact">
      <p class="contact__name">Henrik Audun Strandvik</p>
      <p class="contact__role">Dagligleder og Fotograf</p>
      <ul class="contact__list">
        <li class="contact__item">
          <svg class="contact__icon" viewBox="0 0 16 16" aria-hidden="true"><rect x="4" y="1" width="8" height="14" rx="1.5" fill="none" stroke="#fff" stroke-width="1.6"/><rect x="6.5" y="12" width="3" height="1.2" fill="#fff"/></svg>
          +4791264085
        </li>
        <li class="contact__item">
          <svg class="contact__icon" viewBox="0 0 16 16" aria-hidden="true"><rect x="1" y="4" width="14" height="9" fill="#fff"/><path d="M1 4 L8 9.5 L15 4" fill="none" stroke="var(--brand-blue)" stroke-width="1.2"/></svg>
          post@bildevold.example
        </li>
        <li class="contact__item">
          <svg class="contact__icon" viewBox="0 0 16 16" aria-hidden="true"><circle cx="8" cy="8" r="7" fill="#fff"/><path d="M4 5 Q7 6 6 9 Q9 10 8 14 M10 2.5 Q11 6 14 7" fill="none" stroke="var(--brand-blue)" stroke-width="1.4"/></svg>
          www.bildevold.example
        </li>
      </ul>
      <p class="contact__address">Kvernbakken9, 6040 Fjordvik</p>
    </div>
  </section>

  <section class="card card--back" aria-label="Bakside">
    <div class="back-mark">
      <span class="back-mark__square" aria-hidden="true"></span>
      <span class="back-mark__name">BildeVOLD</span>
    </div>
    <div class="social" aria-hidden="true">
      <span class="social__rule social__rule--left"></span>
      <span class="social__badge"></span>
      <span class="social__badge"></span>
      <span class="social__rule social__rule--right"></span>
    </div>
  </section>

</main>
</body>
</html>
```